Binder design for a veterinary clinic

We are seeking a talented designer to create a standout design for ring binders specifically for our veterinary clinic. These binders will be used to organize materials from our Continuing Professional Development (CPD) projects for colleagues and interns. The design should be clean, professional, and align with our brand guidelines. To give you a better understanding of our branding, we’ve included the design of our vehicles as a reference. As additional reference, please visit www.tierpraxora.at

Target Market(s)

veterinarians

Industry/Entity Type

Veterinary

Font styles to use
Sans Serif

Colors
0054AA
0677BA
7BADD7
CADEEF
E8F1F8
FFC000
F8CF3A
FAE287
FDF2CF
FEFAEE

Requirements
Must have
• Our Logo an a clean design
Should not have
• to much images

```html
<!DOCTYPE html>
<html lang="de">
<head>
<meta charset="utf-8">
<title>Tierpraxora – Ordner Innenseite</title>
<link href="https://fonts.googleapis.com/css2?family=Montserrat:wght@300;400;700&display=swap" rel="stylesheet">
<style>
  :root {
    --backdrop: #e4e4e3;
    --cover-navy: #33465b;
    --cover-edge: #2a3a4c;
    --frame-line: rgba(255,255,255,0.08);
    --headline-grey: #a6adb6;
    --brand-white: #ffffff;
    --brand-gold: #d9a21e;
  }
  * { margin: 0; padding: 0; box-sizing: border-box; }
  html, body {
    width: 1200px; height: 900px; overflow: hidden;
    background: var(--backdrop);
    font-family: "Montserrat", sans-serif;
  }
  .canvas {
    position: relative; width: 1200px; height: 900px;
    display: flex; align-items: center; justify-content: center;
  }
  .binder-cover {
    position: relative;
    width: 600px; height: 800px;
    background: var(--cover-navy);
    border: 3px solid var(--cover-edge);
    border-radius: 4px;
  }
  .cover-frame {
    position: absolute; inset: 28px;
    border: 2px solid var(--frame-line);
  }
  .cover-content {
    position: absolute;
    width: 800px; height: 600px;
    left: 600px; top: 0;
    transform-origin: top left;
    transform: rotate(90deg);
  }
  .welcome {
    position: absolute; left: 160px; top: 70px;
    color: var(--headline-grey);
    font-weight: 300; font-size: 44px; line-height: 1.15;
    letter-spacing: 1px;
  }
  .brand {
    position: absolute; left: 180px; top: 215px;
    display: flex; flex-direction: column; align-items: flex-start;
  }
  .brand-mark {
    width: 120px; height: 120px; border-radius: 50%;
    background: var(--brand-white);
    border: 6px solid var(--brand-gold);
    margin-left: 70px; margin-bottom: 30px;
  }
  .brand-name {
    color: var(--brand-white);
    font-weight: 700; font-size: 50px; line-height: 1;
  }
  .brand-tagline {
    color: var(--brand-gold);
    font-weight: 400; font-size: 24px; letter-spacing: 1px;
    margin-top: 8px;
  }
</style>
</head>
<body>
  <main class="canvas">
    <section class="binder-cover">
      <div class="cover-frame"></div>
      <div class="cover-content">
        <p class="welcome">Herzlich<br>willkommen im</p>
        <div class="brand">
          <div class="brand-mark"></div>
          <p class="brand-name">Tierpraxora</p>
          <p class="brand-tagline">Fachklinik für Kleintiere</p>
        </div>
      </div>
    </section>
  </main>
</body>
</html>
```